Professional Website

We are looking for a new website for our Staffing Company. Attached is a document with all the details and pages needed along with some examples of others websites.

We want a professional Look and feel around the same color theme as the attached Amber Compass.

We currently host our site on PageLoom.io. If the winning designer can also add to PageLoom, that is a plus.

```html
<!DOCTYPE html>
<html lang="en">
<head>
<meta charset="utf-8">
<title>HireBridge Inc – Staffing</title>
<link href="https://fonts.googleapis.com/css2?family=Poppins:wght@400;500;600;700&family=Inter:wght@400&display=swap" rel="stylesheet">
<style>
:root{
  --blue:#2340b5;
  --navy:#2a2f96;
  --ink:#111;
  --text:#333;
  --white:#fff;
  --hero-top:#d9d9d6;
  --hero-bottom:#b9a99a;
}
*{margin:0;padding:0;box-sizing:border-box}
html,body{width:799px;height:1200px;overflow:hidden;background:var(--white)}
body{position:relative;font-family:'Poppins',sans-serif;color:var(--ink)}
a{color:inherit;text-decoration:none}
.topbar{position:absolute;left:0;top:0;width:799px;height:41px;background:var(--blue);color:var(--white)}
.hotline{position:absolute;left:77px;top:10px;font-size:15px;font-weight:500;display:flex;align-items:center;gap:4px}
.logins{position:absolute;right:75px;top:5px;display:flex;gap:9px}
.login-btn{width:104px;height:29px;border:1px solid var(--white);font-size:10px;font-weight:500;display:flex;align-items:center;justify-content:center}
.navbar{position:absolute;left:0;top:41px;width:799px;height:47px;background:var(--white)}
.brand{position:absolute;left:75px;top:5px;color:var(--blue);font-weight:700;font-size:25px;line-height:1;letter-spacing:-.5px}
.brand small{display:block;font-size:7px;font-weight:500;letter-spacing:.5px;margin-top:2px}
.menu{position:absolute;right:75px;top:17px;display:flex;gap:35px;font-size:11px;font-weight:500}
.hero{position:absolute;left:0;top:88px;width:799px;height:424px;background:linear-gradient(180deg,var(--hero-top) 0%,#c9c7c2 55%,var(--hero-bottom) 100%)}
.hero-title{position:absolute;left:0;top:62px;width:799px;text-align:center;color:var(--blue);font-size:28px;font-weight:600;line-height:36px}
.cards{position:absolute;left:74px;top:438px;width:651px;height:243px;display:flex}
.card{flex:1;color:var(--white);text-align:center;padding-top:30px}
.card-seek{background:var(--blue)}
.card-hire{background:var(--navy)}
.card h2{font-size:17px;font-weight:600;margin:12px 0 10px}
.card p{font-family:'Inter',sans-serif;font-size:10px;line-height:20.5px;letter-spacing:-.2px}
.card-btn{display:inline-block;margin-top:17px;width:109px;height:31px;line-height:31px;background:var(--white);color:var(--blue);font-size:11px;font-weight:500;border-radius:2px}
.welcome{position:absolute;left:100px;top:728px;width:599px;text-align:center}
.welcome h1{font-size:23px;font-weight:600}
.welcome p{font-family:'Inter',sans-serif;font-size:11px;color:var(--text);line-height:23.4px;margin-top:6px;text-align:justify;text-align-last:center;letter-spacing:-.15px}
.footer{position:absolute;left:0;top:938px;width:799px;height:262px;background:var(--navy);color:var(--white)}
.footer .brand{color:var(--white);left:74px;top:50px;font-size:31px}
.footer .brand small{font-size:8px}
.f-hotline{position:absolute;left:76px;top:116px;font-size:13px;display:flex;gap:5px;align-items:center}
.col{position:absolute;top:52px;font-size:10.5px}
.col h3{font-size:12.5px;font-weight:600;margin-bottom:7px}
.col li{list-style:none;line-height:23.4px}
.social li{display:flex;align-items:center;gap:9px;line-height:29px;font-size:10px}
.dot{width:19px;height:19px;border-radius:50%;background:#3a3fae}
.rule{position:absolute;left:74px;top:214px;width:651px;height:1px;background:#4a4fb0}
.copy{position:absolute;left:0;top:230px;width:799px;text-align:center;font-family:'Inter',sans-serif;font-size:9.5px}
</style>
</head>
<body>
<header class="topbar">
  <div class="hotline">
    <svg width="12" height="12" viewBox="0 0 24 24" fill="#fff"><path d="M6.6 10.8a15.1 15.1 0 0 0 6.6 6.6l2.2-2.2a1 1 0 0 1 1-.25 11.4 11.4 0 0 0 3.6.57 1 1 0 0 1 1 1V20a1 1 0 0 1-1 1A17 17 0 0 1 3 4a1 1 0 0 1 1-1h3.5a1 1 0 0 1 1 1c0 1.25.2 2.45.57 3.6a1 1 0 0 1-.25 1z"/></svg>
    Our&nbsp; Hotline # 555-014-2290
  </div>
  <nav class="logins">
    <a class="login-btn" href="#">Employee Login</a>
    <a class="login-btn" href="#">Swift Card Login</a>
    <a class="login-btn" href="#">Harbor Bank Login</a>
  </nav>
</header>
<div class="navbar">
  <div class="brand">HireBridge Inc<small>CLERICAL &amp; INDUSTRIAL</small></div>
  <nav class="menu">
    <a href="#">HOME</a><a href="#">ABOUT</a><a href="#">JOB ⌄</a><a href="#">OFFICE INFO</a><a href="#">CONTACT US</a>
  </nav>
</div>
<section class="hero" role="img" aria-label="Photo of a smiling team of five professionals working on laptops at a meeting table">
  <h1 class="hero-title">Recruiting Agency For Temporary<br>And Direct Hire Employees</h1>
</section>
<section class="cards">
  <div class="card card-seek">
    <svg width="50" height="50" viewBox="0 0 50 50" fill="none" stroke="#fff" stroke-width="1.8"><rect x="6" y="16" width="38" height="26" rx="3"/><path d="M18 16v-5h14v5M6 27h38"/><rect x="22" y="24" width="6" height="6"/></svg>
    <h2>I’m looking for a Job</h2>
    <p>Lorem ipsum dolor sit amet, consectetur adipiscing elit,<br>sed do eiusmod tempor incididunt ut labore</p>
    <a class="card-btn" href="#">Find a Job</a>
  </div>
  <div class="card card-hire" style="padding-top:26px">
    <svg width="50" height="50" viewBox="0 0 50 50" fill="none" stroke="#fff" stroke-width="1.8"><rect x="10" y="8" width="30" height="36" rx="3"/><path d="M20 8v-3h10v3M17 34h16M17 39h10"/><circle cx="25" cy="21" r="6"/></svg>
    <h2 style="margin-top:8px">I need Employees</h2>
    <p>Lorem ipsum dolor sit amet, consectetur adipiscing elit,<br>sed do eiusmod tempor incididunt ut labore</p>
    <a class="card-btn" href="#">Employees</a>
  </div>
</section>
<section class="welcome">
  <h1>Welcome To HireBridge Inc</h1>
  <p>We need a short paragraph that summarizes how we are awesome! Greatest part of our daily job is that we are constantly bringing people together. Our Clients come to us in search of the perfect candidate and the job hunters approach us when they are in need of a job or looking for their next exciting role. Being able to work with and connect the two is incredibly satisfying. Not to mention that in today's current job market, employers are fighting for the top talent. This makes our employees and partners grateful for the help in finding it!</p>
</section>
<footer class="footer">
  <div class="brand">HireBridge Inc<small>CLERICAL &amp; INDUSTRIAL</small></div>
  <div class="f-hotline">
    <svg width="11" height="11" viewBox="0 0 24 24" fill="#fff"><path d="M6.6 10.8a15.1 15.1 0 0 0 6.6 6.6l2.2-2.2a1 1 0 0 1 1-.25 11.4 11.4 0 0 0 3.6.57 1 1 0 0 1 1 1V20a1 1 0 0 1-1 1A17 17 0 0 1 3 4a1 1 0 0 1 1-1h3.5a1 1 0 0 1 1 1c0 1.25.2 2.45.57 3.6a1 1 0 0 1-.25 1z"/></svg>
    Hotline # 555-014-2290
  </div>
  <div class="col" style="left:334px"><h3>Quick Links</h3><ul><li>Home</li><li>About</li><li>Job</li><li>Office Info</li><li>Contact Us</li></ul></div>
  <div class="col" style="left:476px"><h3>Areas we service</h3><ul><li>Blue Island</li><li>Alsip</li><li>Romeoville</li></ul></div>
  <div class="col social" style="left:654px;top:51px"><h3>Follow Us</h3><ul><li><span class="dot"></span>Friendwall</li><li><span class="dot"></span>Chirper</li><li><span class="dot"></span>Worknet</li><li><span class="dot"></span>Snapgram</li></ul></div>
  <div class="rule"></div>
  <div class="copy">©Copyright ©2022 hirebridge inc. All Rights Reserved.</div>
</footer>
</body>
</html>
```